Copperleaf Roofing Business Card

This is my current business card. But I’d like to make some changes. Somewhere on the card I’d like to list some of the services we offer. Maybe on the back? But I’d still like to keep the red. White and black modern look.

-residential & commercial roofing
-Roof Repairs & Maintenance
-Storm Damage & Insurance Claims specialist
-Christmas Lights and permanent Christmas lights
Fencing. Windows. Gutters. Siding. Sheetrock, painting.

```html
<!DOCTYPE html>
<html lang="en">
<head>
<meta charset="utf-8">
<title>Copperleaf Roofing Co. – Business Card</title>
<link rel="stylesheet" href="https://fonts.googleapis.com/css2?family=Orbitron:wght@800&family=Poppins:wght@400;600&display=swap">
<style>
  :root {
    --page: #e3e6e7;
    --card: #161616;
    --red: #e8202a;
    --red-dark: #8e1418;
    --white: #ffffff;
    --text: #f2f2f2;
  }
  * { box-sizing: border-box; margin: 0; padding: 0; }
  html, body { width: 1200px; height: 960px; overflow: hidden; background: var(--page); }
  body { position: relative; font-family: "Poppins", sans-serif; }

  .card {
    position: absolute; left: 250px; width: 701px; height: 400px;
    background: var(--card); border-radius: 28px; overflow: hidden;
  }
  .card--front { top: 60px; }
  .card--back { top: 500px; }

  .side-bar { position: absolute; top: 100px; width: 16px; height: 200px; background: var(--red); }
  .side-bar--left { left: 0; }
  .side-bar--right { right: 0; }

  .brand { position: absolute; text-align: center; }
  .brand-mark { display: block; margin: 0 auto; border-radius: 50%; background: var(--red); }
  .brand-name {
    font-family: "Poppins", sans-serif; font-weight: 600; color: var(--white);
    text-transform: uppercase; line-height: 1.1; letter-spacing: 1px;
  }
  .brand-name .line-1 { display: block; font-size: 28px; }
  .brand-name .line-2 { display: block; font-size: 19px; letter-spacing: 2px; }

  .card--front .brand { left: 0; width: 100%; top: 27px; }
  .card--front .brand-mark { width: 108px; height: 108px; margin-bottom: 10px; }

  .services { position: absolute; left: 0; width: 100%; top: 238px; text-align: center; color: var(--text); }
  .services h2 { font-weight: 600; font-size: 18px; color: var(--red); letter-spacing: 0.5px; line-height: 22px; }
  .services li { list-style: none; font-size: 15.5px; line-height: 22.8px; letter-spacing: 0.4px; }

  .card--back .brand { left: 40px; width: 270px; top: 105px; }
  .card--back .brand-mark { width: 120px; height: 120px; margin-bottom: 14px; }
  .card--back .brand-name .line-1 { font-size: 30px; }
  .card--back .brand-name .line-2 { font-size: 20px; }

  .divider { position: absolute; left: 350px; top: 94px; width: 1px; height: 212px; background: var(--red-dark); }

  .contact-block { position: absolute; left: 401px; top: 118px; }
  .person-name {
    font-family: "Orbitron", sans-serif; font-weight: 800; font-size: 25px;
    text-transform: uppercase; color: var(--white); letter-spacing: 1px; line-height: 1;
  }
  .person-name .first { color: var(--red); }
  .person-role { margin-top: 10px; font-weight: 600; font-size: 16px; color: var(--white); letter-spacing: 1px; }
  .contact-list { margin-top: 40px; list-style: none; }
  .contact-list li {
    display: flex; align-items: center; gap: 9px;
    font-size: 17px; line-height: 23px; color: var(--text); letter-spacing: 0.3px;
  }
  .contact-list svg { width: 16px; height: 16px; flex: none; }
</style>
</head>
<body>

  <section class="card card--front" aria-label="Card front">
    <span class="side-bar side-bar--left"></span>
    <span class="side-bar side-bar--right"></span>

    <div class="brand">
      <span class="brand-mark"></span>
      <p class="brand-name"><span class="line-1">Copperleaf</span><span class="line-2">Roofing Co.</span></p>
    </div>

    <div class="services">
      <h2>SERVICES WE OFFER</h2>
      <ul>
        <li>Roof Repairs &amp; Maintenance</li>
        <li>Residential &amp; Commercial Roofing</li>
        <li>Storm Damage &amp; Insurance Claims Specialist</li>
        <li>Christmas Lights and Permanent Christmas lights</li>
        <li>Fencing. Windows. Gutters. Siding. Sheetrock, Painting</li>
      </ul>
    </div>
  </section>

  <section class="card card--back" aria-label="Card back">
    <span class="side-bar side-bar--left"></span>
    <span class="side-bar side-bar--right"></span>

    <div class="brand">
      <span class="brand-mark"></span>
      <p class="brand-name"><span class="line-1">Copperleaf</span><span class="line-2">Roofing Co.</span></p>
    </div>

    <span class="divider"></span>

    <div class="contact-block">
      <p class="person-name"><span class="first">Dean</span> Mercer</p>
      <p class="person-role">OWNER</p>
      <ul class="contact-list">
        <li>
          <svg viewBox="0 0 24 24" aria-hidden="true"><path fill="#e8202a" d="M6.6 10.8a15.1 15.1 0 0 0 6.6 6.6l2.2-2.2a1 1 0 0 1 1-.25 11.4 11.4 0 0 0 3.6.57 1 1 0 0 1 1 1V20a1 1 0 0 1-1 1A17 17 0 0 1 3 4a1 1 0 0 1 1-1h3.5a1 1 0 0 1 1 1c0 1.25.2 2.45.57 3.57a1 1 0 0 1-.25 1z"/></svg>
          555-014-2293
        </li>
        <li>
          <svg viewBox="0 0 24 24" aria-hidden="true"><g fill="none" stroke="#e8202a" stroke-width="2"><circle cx="12" cy="12" r="9.5"/><ellipse cx="12" cy="12" rx="4" ry="9.5"/><path d="M2.5 12h19M4 7h16M4 17h16"/></g></svg>
          www.copperleafroofing.co
        </li>
        <li>
          <svg viewBox="0 0 24 24" aria-hidden="true"><g fill="none" stroke="#e8202a" stroke-width="2"><rect x="2.5" y="5" width="19" height="14" rx="1.5"/><path d="M3 6l9 7 9-7"/></g></svg>
          Dean@copperleafroofing.co
        </li>
      </ul>
    </div>
  </section>

</body>
</html>
```